Accountability Project Graphics

I want to create 10 social media graphics (new Instagram size 4:5 (1080 x 1350 pixels) focusing on our Quilvo Accountability App, using any of the 3 pictures attached. Use the attached pics only, NO RANDOM STOCK PHOTOGRAPHY. For the color scheme, use the landing page colors/fonts (attached).
You can add any of the 3 photos attached but I mainly need BOLD text that includes these headlines and sub-headlines on them.
Please NOTE for all the headlines below, also add this sub-headline on each graphic:
Stay Consistent with RT in Your Pocket!
Here are the headlines:
• Stop Starting Over Every Monday
• You don't need more willpower. You need more support
• Built for women who are tired of doing this alone
• When Motivation Fades, RT Checks In
• The Support System You've Been Missing
• Support When Motivation Disappears
• What if RT Checked in Every Day?
• The Missing Piece Isn't Another Diet
• Eat the food you love. Stay accountable every day.
• One Bad Meal Doesn't Mean You Failed
women over 40 trying to lose weight

```html
<!DOCTYPE html>
<html lang="en">
<head>
<meta charset="utf-8">
<title>Accountability Project Graphics</title>
<link rel="stylesheet" href="https://fonts.googleapis.com/css2?family=Playfair+Display:wght@700&family=Poppins:ital,wght@1,400;1,500&display=swap">
<style>
  :root {
    --page-bg: #e6e6e6;
    --blush: #fdd0dc;
    --rose: #c65b7c;
    --plum: #2e1f3f;
    --ink: #2e1f3f;
    --white: #ffffff;
    --divider: #e0607f;
    --divider-light: #f3b8c8;
  }
  * { margin: 0; padding: 0; box-sizing: border-box; }
  html, body { width: 1200px; height: 2785px; overflow: hidden; background: var(--page-bg); }
  .board { position: relative; width: 1200px; height: 2785px; }
  .post {
    position: absolute; width: 371px;
    display: flex; flex-direction: column; overflow: hidden;
  }
  .col-left { left: 222px; }
  .col-right { left: 603px; }
  .photo { flex: none; width: 100%; }
  .photo-portrait { background: linear-gradient(100deg, #7a6a58 0%, #3a2e2a 35%, #1d1a22 55%, #2f3a24 80%, #5d7240 100%); }
  .photo-duo { background: linear-gradient(100deg, #a9a8a4 0%, #ece4da 20%, #2a3550 42%, #f2f0ee 52%, #3a4d72 70%, #f3e6d6 100%); }
  .photo-hug { background: linear-gradient(110deg, #e6a8c8 0%, #c9a2b0 25%, #2a2026 45%, #d94f8a 65%, #e3c4ea 100%); }
  .panel {
    flex: 1; display: flex; flex-direction: column;
    align-items: center; justify-content: center; text-align: center;
    padding: 8px 6px 10px;
  }
  .panel-blush { background: var(--blush); color: var(--ink); }
  .panel-rose { background: var(--rose); color: var(--white); }
  .panel-plum { background: var(--plum); color: var(--white); }
  .headline {
    font-family: "Playfair Display", serif; font-weight: 700;
    font-size: 31px; line-height: 1.2; letter-spacing: -0.2px;
    white-space: nowrap;
  }
  .headline-tight { font-size: 29px; letter-spacing: -0.4px; }
  .divider { width: 68px; height: 1.5px; background: var(--divider); margin: 16px 0 18px; }
  .panel-rose .divider { background: var(--divider-light); }
  .tagline {
    font-family: "Poppins", sans-serif; font-style: italic; font-weight: 500;
    font-size: 13px; letter-spacing: 0.3px; white-space: nowrap;
  }
</style>
</head>
<body>
<main class="board">

  <article class="post col-left" style="top:197px;height:464px">
    <div class="photo photo-portrait" style="height:270px" role="img" aria-label="Coach smiling in a black lace top, hand on hip"></div>
    <div class="panel panel-blush">
      <h2 class="headline">Stop Starting Over<br>Every Monday</h2>
      <span class="divider"></span>
      <p class="tagline">Stay Consistent with RT in Your Pocket!</p>
    </div>
  </article>

  <article class="post col-right" style="top:197px;height:464px">
    <div class="photo photo-duo" style="height:244px" role="img" aria-label="Coach and client laughing together side by side"></div>
    <div class="panel panel-rose">
      <h2 class="headline headline-tight">You Don't Need More<br>Willpower. You Need<br>More Support</h2>
      <span class="divider"></span>
      <p class="tagline">Stay Consistent with RT in Your Pocket!</p>
    </div>
  </article>

  <article class="post col-left" style="top:672px;height:464px">
    <div class="photo photo-hug" style="height:230px" role="img" aria-label="Coach joyfully hugging a client"></div>
    <div class="panel panel-plum">
      <h2 class="headline">Built For Women<br>Who Are Tired Of<br>Doing&nbsp; This Alone</h2>
      <span class="divider"></span>
      <p class="tagline">Stay Consistent with RT in Your Pocket!</p>
    </div>
  </article>

  <article class="post col-right" style="top:672px;height:464px">
    <div class="photo photo-duo" style="height:276px" role="img" aria-label="Coach and client laughing together side by side"></div>
    <div class="panel panel-blush">
      <h2 class="headline">When Motivation<br>Fades, Rt Checks In</h2>
      <span class="divider"></span>
      <p class="tagline">Stay Consistent with RT in Your Pocket!</p>
    </div>
  </article>

  <article class="post col-left" style="top:1148px;height:464px">
    <div class="photo photo-portrait" style="height:277px" role="img" aria-label="Coach smiling in a black lace top, hand on hip"></div>
    <div class="panel panel-plum">
      <h2 class="headline">The Support System<br>You've Been Missing</h2>
      <span class="divider"></span>
      <p class="tagline">Stay Consistent with RT in Your Pocket!</p>
    </div>
  </article>

  <article class="post col-right" style="top:1148px;height:464px">
    <div class="photo photo-hug" style="height:277px" role="img" aria-label="Coach joyfully hugging a client"></div>
    <div class="panel panel-rose">
      <h2 class="headline headline-tight">Support When<br>Motivation Disappears</h2>
      <span class="divider"></span>
      <p class="tagline">Stay Consistent with RT in Your Pocket!</p>
    </div>
  </article>

  <article class="post col-left" style="top:1623px;height:462px">
    <div class="photo photo-portrait" style="height:280px" role="img" aria-label="Coach smiling in a black lace top, hand on hip"></div>
    <div class="panel panel-blush">
      <h2 class="headline">What If Rt Checked<br>In Every Day?</h2>
      <span class="divider"></span>
      <p class="tagline">Stay Consistent with RT in Your Pocket!</p>
    </div>
  </article>

  <article class="post col-right" style="top:1623px;height:462px">
    <div class="photo photo-duo" style="height:282px" role="img" aria-label="Coach and client laughing together side by side"></div>
    <div class="panel panel-plum">
      <h2 class="headline">The Missing Piece<br>Isn't Another Diet</h2>
      <span class="divider"></span>
      <p class="tagline">Stay Consistent with RT in Your Pocket!</p>
    </div>
  </article>

  <article class="post col-left" style="top:2098px;height:463px">
    <div class="photo photo-duo" style="height:243px" role="img" aria-label="Coach and client laughing together side by side"></div>
    <div class="panel panel-plum">
      <h2 class="headline headline-tight">Eat The Food You<br>Love. Stay Accountable<br>Every Day.</h2>
      <span class="divider"></span>
      <p class="tagline">Stay Consistent with RT in Your Pocket!</p>
    </div>
  </article>

  <article class="post col-right" style="top:2098px;height:463px">
    <div class="photo photo-hug" style="height:288px" role="img" aria-label="Coach joyfully hugging a client"></div>
    <div class="panel panel-rose">
      <h2 class="headline headline-tight">One Bad Meal Doesn't<br>Mean You Failed</h2>
      <span class="divider"></span>
      <p class="tagline">Stay Consistent with RT in Your Pocket!</p>
    </div>
  </article>

</main>
</body>
</html>
```